Brookvale Building Company - advertisement poster

I am looking to print some canvas signs to advertise my general contracting company, Brookvale Building Company. The sign will measure 6' long x 3' high so the size should match that ratio. I already have a logo icon, which is the Letter 'B' and some trees that I would like to incorporate, see attached. I would also like the to have the following information listed:
1) phone number: 831-555-0172
2) email: brookvalebuildingcompany@mailnest.example
3) website: brookvalebuildingcompany.example
4) Lic#4826130
5) I want to use this text: "BUILD WITH THE B-CREW!"

The ad should be relatively simple and clean. Black and Green are my company colors. I am open to creative ideas!

Target Market(s)

People looking to renovate their homes

Industry/Entity Type

Construction

Colors
59FF00
82FF00
B8FF75
E3FFCB
F4FFEA

Requirements
Must have
• Must have my company logo
Should not have
• No photos or complex graphics

```html
<!DOCTYPE html>
<html lang="en">
<head>
<meta charset="utf-8">
<title>Brookvale Building Company – Sign</title>
<link rel="stylesheet" href="https://fonts.googleapis.com/css2?family=Arimo:wght@400;700&display=swap">
<style>
  :root {
    --backdrop: #3b4048;
    --sign-black: #1c1c1c;
    --brand-green: #5cb83f;
    --text-white: #ffffff;
  }
  * { box-sizing: border-box; margin: 0; padding: 0; }
  html, body {
    width: 1200px;
    height: 800px;
    overflow: hidden;
    background: var(--backdrop);
  }
  .canvas {
    position: relative;
    width: 1200px;
    height: 800px;
  }
  .sign {
    position: absolute;
    left: 40px;
    top: 120px;
    width: 1120px;
    height: 560px;
    background: var(--sign-black);
    font-family: "Arimo", Arial, sans-serif;
    color: var(--text-white);
  }
  .headline {
    position: absolute;
    top: 70px;
    left: 0;
    width: 100%;
    text-align: center;
    font-weight: 700;
    line-height: 0.98;
    letter-spacing: 1px;
  }
  .headline__lead {
    display: block;
    color: var(--brand-green);
    font-size: 104px;
    padding-left: 60px;
  }
  .headline__crew {
    display: block;
    color: var(--text-white);
    font-size: 104px;
    padding-left: 90px;
  }
  .brand {
    position: absolute;
    left: 140px;
    top: 392px;
    display: flex;
    align-items: center;
    gap: 18px;
  }
  .brand__mark {
    width: 66px;
    height: 66px;
    background: var(--brand-green);
    flex: none;
  }
  .brand__name {
    font-weight: 700;
    font-size: 28px;
    line-height: 1.1;
    color: var(--text-white);
    text-transform: uppercase;
    letter-spacing: 1px;
  }
  .contact {
    position: absolute;
    left: 580px;
    top: 366px;
    display: flex;
    flex-direction: column;
    gap: 6px;
  }
  .contact__web {
    font-size: 24px;
    letter-spacing: 0.5px;
  }
  .contact__phone {
    font-size: 40px;
    font-weight: 700;
    color: var(--brand-green);
    letter-spacing: 4px;
  }
  .contact__email {
    font-size: 19px;
    letter-spacing: 0.5px;
  }
  .contact__license {
    font-size: 17px;
    letter-spacing: 1px;
    color: var(--brand-green);
  }
</style>
</head>
<body>
  <main class="canvas">
    <section class="sign">
      <h1 class="headline">
        <span class="headline__lead">BUILD WITH THE</span>
        <span class="headline__crew">B-CREW!</span>
      </h1>

      <div class="brand">
        <span class="brand__mark"></span>
        <span class="brand__name">Brookvale<br>Building Company</span>
      </div>

      <div class="contact">
        <p class="contact__web">BrookvaleBuildingCompany.example</p>
        <p class="contact__phone">831-555-0172</p>
        <p class="contact__email">brookvalebuildingcompany@mailnest.example</p>
        <p class="contact__license">Lic#4826130</p>
      </div>
    </section>
  </main>
</body>
</html>
```